Mortgage Protection Insurance Flyer

The target audience are new home owners so the design needs to be clean and simple.

This a primarily for Final Expense Insurance, but need an area where it says "We Also Specialize In:"
- Medicare Supplement Insurance (MediGap)
- Annuities
- Final Expense

All flyer versions need to be editable. Colors to be used are red, white or black. Refer to my website for colors and photos (corvantshield.com). Will attach my logo and a flyer that I found online that is the format that I am looking for (for 8.5 in. x 11 in version). Need flyer in standard letter size 8.5 in. x11 in. but also in 8.5 in. x 5.5 in and 5.0 in. x 8.0 in. All sizes to be portrait oriented. If picked as winning design, need all flyer versions in full color, also in grey scale and files in all industry file types.

Content can be taken from my website..... corvantshield.com

Do NOT submit if you are not willing to provide all versions as described above for the original project price.

Must use royalty-free stock photos please.

Target Market(s)

New homeowners looking for insurance to protect there mortgage payments

Industry/Entity Type

Life Insurance

Colors
f69fa3

Requirements
Must have
• Colors to be used are red, white or black.
• Need flyer in standard letter size 8.5 in. x11 in. but also in 3.5 in. x 8.5 in (Full Bleed 3.75 in by 8.75 in.) and 4.0 in. x 6.0 in. (Full Bleed 4.12 in x 6.12 in) Each design tailored to the size dimensions (So no squeezing 8.5 x 11 design into a 4.0 x 6.0 space.) All sizes to be portrait oriented. If picked as winning design, need all flyer versions in full color, also in grey scale and files in all file types.
• Do not need physical address on flyer, do need email address on flyer though - tkelwer@corvantshield.com
• So phone number should be prominent, email address and website address should also be contact area.
• If you can not agree to terms above, do not submit any designs.
• Need facebook & twitter logos somewhere in contact info area.
Nice to have
• See sample flyers I have attached.
• White background with red used as primary graphic color and black used as secondary graphic if needed.
• font to be used should similar to one used in logo.

```html
<!DOCTYPE html>
<html lang="en">
<head>
<meta charset="utf-8">
<title>Corvant Shield Insurance – Final Expense Flyer, 8.5 x 11</title>
<link rel="stylesheet" href="https://fonts.googleapis.com/css2?family=Oswald:wght@500;700&family=Roboto:wght@400;500;700&family=Montserrat:wght@300&display=swap">
<style>
  :root {
    --canvas: #d6d6d6;
    --label: #6a6a6a;
    --ink: #1c1c1c;
    --body: #3a3a3a;
    --paper: #ffffff;
    --row-bg: #d9d9d9;
  }
  .flyer {
    --accent: #e3141b;
    --accent-dark: #8e1016;
    --box-top: #f20f16;
    --box-bottom: #b0121a;
    --photo-a: #f3efec;
    --photo-b: #d9c2b4;
    --photo-c: #a88c7c;
  }
  .flyer--mono {
    --accent: #6e6e6e;
    --accent-dark: #454545;
    --box-top: #7c7c7c;
    --box-bottom: #545454;
    --photo-a: #f2f2f2;
    --photo-b: #c6c6c6;
    --photo-c: #8d8d8d;
  }
  .flyer--mono .headline__accent { color: #787878; }
  .flyer--mono .section-title { color: #555; }

  * { box-sizing: border-box; margin: 0; padding: 0; }
  html, body { width: 1200px; height: 1200px; overflow: hidden; }
  body { background: var(--canvas); position: relative; font-family: "Roboto", Arial, sans-serif; }

  .size-label {
    position: absolute; top: 96px; left: 0; width: 1200px; text-align: center;
    font-family: "Montserrat", Arial, sans-serif; font-weight: 300; font-size: 40px; color: var(--label);
  }

  .flyer {
    position: absolute; top: 278px; width: 502px; height: 645px;
    background: var(--paper); overflow: hidden; color: var(--body);
  }
  .flyer--color { left: 85px; }
  .flyer--mono { left: 614px; }

  .flyer__art { position: absolute; inset: 0; width: 502px; height: 645px; }

  .brand {
    position: absolute; left: 26px; top: 34px; display: flex; align-items: center; gap: 6px;
    font-family: "Oswald", Arial, sans-serif; font-weight: 700; font-size: 19px; letter-spacing: .5px;
    color: var(--ink); text-transform: uppercase;
  }
  .brand__mark { width: 11px; height: 11px; background: var(--accent); }

  .headline {
    position: absolute; left: 25px; top: 128px;
    font-family: "Oswald", Arial, sans-serif; font-weight: 700; text-transform: uppercase;
    color: var(--ink); line-height: 1;
  }
  .headline__line { display: block; }
  .headline__top { font-size: 40px; }
  .headline__accent { font-size: 36px; color: var(--accent); margin-top: 2px; }
  .headline__bottom { font-size: 23px; font-weight: 500; margin-top: 5px; }

  .benefits {
    position: absolute; left: 292px; top: 216px; width: 190px; height: 229px;
    border-radius: 16px; background: linear-gradient(180deg, var(--box-top), var(--box-bottom));
    box-shadow: 0 2px 4px rgba(0,0,0,.25);
  }
  .benefits__tab {
    position: absolute; left: 283px; top: 235px; width: 84px; height: 19px;
    background: #2b2b2b; border-radius: 0 10px 10px 0; color: #fff;
    font-family: "Roboto", Arial, sans-serif; font-weight: 700; font-size: 14px; line-height: 19px; padding-left: 7px;
  }
  .benefits__list { position: absolute; left: 311px; top: 267px; width: 166px; list-style: none; }
  .benefits__list li {
    position: relative; padding-left: 11px; color: #fff; font-size: 7.4px; font-weight: 500;
    line-height: 9.4px; margin-bottom: 9.8px;
  }

  .check::before {
    content: ""; position: absolute; left: 0; top: 1px; width: 7px; height: 7px;
    border: 1px solid currentColor; border-radius: 50%;
  }
  .check::after {
    content: ""; position: absolute; left: 2.4px; top: 2.6px; width: 2.4px; height: 1.3px;
    border-left: 1px solid currentColor; border-bottom: 1px solid currentColor; transform: rotate(-45deg);
  }

  .section-title {
    position: absolute; font-weight: 700; font-size: 10.5px; color: var(--accent);
  }
  .section-title--final { left: 25px; top: 296px; }
  .section-title--also { left: 298px; top: 460px; }

  .copy { position: absolute; left: 25px; width: 240px; font-size: 7.4px; line-height: 9.6px; }
  .copy--intro { top: 318px; }
  .copy--p1 { top: 414px; }
  .copy--p2 { top: 463px; }
  .copy--p3 { top: 492px; }
  .copy--p4 { top: 521px; }

  .rates { position: absolute; left: 25px; top: 367px; width: 232px; border-collapse: separate; border-spacing: 0 6px; margin-top: -6px; font-size: 7px; }
  .rates th { background: var(--row-bg); text-align: left; font-weight: 500; padding: 0 5px; height: 12px; width: 157px; color: #222; }
  .rates td { background: var(--accent); color: #fff; text-align: center; font-weight: 700; border-left: 2px solid #fff; }

  .also-list { position: absolute; left: 302px; top: 482px; list-style: none; }
  .also-list li { position: relative; padding-left: 11px; font-size: 8.2px; line-height: 10px; margin-bottom: 4.4px; color: #333; }
  .also-list .check::before, .also-list .check::after { color: var(--accent); }

  .footnote { position: absolute; left: 298px; top: 531px; width: 185px; font-size: 5.4px; line-height: 6.6px; color: #444; }

  .call { position: absolute; left: 26px; top: 575px; color: #fff; }
  .call__label { font-size: 16px; font-weight: 500; display: block; }
  .call__phone { font-size: 26px; font-weight: 700; letter-spacing: -.3px; display: block; line-height: 1.05; }

  .contact { position: absolute; top: 594px; display: flex; align-items: center; gap: 5px; color: #fff; font-size: 6.6px; font-weight: 700; }
  .contact--email { left: 221px; }
  .contact--web { left: 373px; }
  .contact__icon { width: 18px; height: 18px; border: 1px solid #fff; border-radius: 50%; display: flex; align-items: center; justify-content: center; }

  .social { position: absolute; left: 460px; top: 617px; display: flex; gap: 2px; }
  .social span { width: 7px; height: 7px; background: #fff; border-radius: 1px; }
</style>
</head>
<body>

<div class="size-label">8.5x 11</div>

<!-- Full colour version -->
<article class="flyer flyer--color">
  <svg class="flyer__art" viewBox="0 0 502 645" aria-hidden="false">
    <defs>
      <linearGradient id="photoColor" x1="0" y1="0" x2="1" y2="0">
        <stop offset="0" stop-color="#f3efec"/><stop offset=".55" stop-color="#d9c2b4"/><stop offset="1" stop-color="#a88c7c"/>
      </linearGradient>
      <linearGradient id="footColor" x1="0" y1="0" x2="0" y2="1">
        <stop offset="0" stop-color="#e3141b"/><stop offset="1" stop-color="#8e1016"/>
      </linearGradient>
    </defs>
    <rect x="0" y="0" width="502" height="272" fill="url(#photoColor)" role="img" aria-label="Photo: smiling senior couple embracing in a bright home"/>
    <path d="M0 0 H275 C230 50 150 100 0 110 Z" fill="#fff"/>
    <path d="M288 0 C242 55 150 107 0 116" fill="none" stroke="#e3141b" stroke-width="2.5"/>
    <path d="M277 0 C232 51 150 101 0 111" fill="none" stroke="#1c1c1c" stroke-width="4"/>
    <path d="M0 262 C120 274 250 272 330 250 S460 218 502 224 V645 H0 Z" fill="#fff"/>
    <path d="M0 250 C120 262 250 260 330 238 S460 206 502 212" fill="none" stroke="#1c1c1c" stroke-width="6"/>
    <path d="M0 259 C120 271 250 269 330 247 S460 215 502 221" fill="none" stroke="#e3141b" stroke-width="3"/>
    <path d="M0 590 C120 555 250 560 330 575 S460 560 502 530 V645 H0 Z" fill="url(#footColor)"/>
    <path d="M0 578 C120 543 250 548 330 563 S460 547 502 518" fill="none" stroke="#1c1c1c" stroke-width="4"/>
  </svg>

  <div class="brand"><span class="brand__mark"></span>Corvant Shield</div>

  <h1 class="headline">
    <span class="headline__line headline__top">Our</span>
    <span class="headline__line headline__accent">Plans Are</span>
    <span class="headline__line headline__bottom">Based on Yours</span>
  </h1>

  <div class="benefits"></div>
  <div class="benefits__tab">Benefits:</div>
  <ul class="benefits__list">
    <li class="check">All plans we offer are state regulated</li>
    <li class="check">Relatively low monthly premiums</li>
    <li class="check">Premiums can never increase</li>
    <li class="check">Your policy can never be cancelled as long as you pay your premium</li>
    <li class="check">No medical exams</li>
    <li class="check">Guaranteed Death Benefit</li>
    <li class="check">Many policies we offer are Guaranteed Acceptance, "Day 1" coverage, have a child/grandchild rider and/or have an accelerated death benefit rider</li>
  </ul>

  <h2 class="section-title section-title--final">Final Expense Insurance</h2>
  <p class="copy copy--intro">Final Expense Insurance is a type of permanent whole life insurance insurance where the death benefit is used to cover (but not limited to) medical costs, funeral costs and other end-of-life expenses. It is a budget friendly option with a death benefit of up to $40k.</p>
  <table class="rates">
    <tr><th>Monthly premiums as low as</th><td>$11*</td></tr>
    <tr><th>Death Benefits as high as</th><td>$40,000</td></tr>
  </table>
  <p class="copy copy--p1">Unforeseen events and a lack of the right kind of insurance can spell trouble quickly. Contact us today, to set up a free assessment time. We will analyze your insurance needs and get you and your family the right coverage quickly at a budget friendly price.</p>
  <p class="copy copy--p2">We have been helping clients in Northern Idaho/Eastern Washington prepare for the unknown.</p>
  <p class="copy copy--p3">We have access to the industry's top insurance carriers so you can get the right coverage, that fits your budget.</p>
  <p class="copy copy--p4">Find out how we can give you the peace of mind of knowing your family will not have a financial burden if something were to happen to you.</p>

  <h2 class="section-title section-title--also">We Also Specialize In:</h2>
  <ul class="also-list">
    <li class="check">Medicare Supplement Insurance (Medigap)</li>
    <li class="check">Annuities</li>
    <li class="check">Mortgage Protection Insurance</li>
  </ul>
  <p class="footnote">*Based on an insured that is a 65 year old, non-smoking female that has no medical conditions with a death benefit of $2k</p>

  <div class="call"><span class="call__label">Call us now:</span><span class="call__phone">(208)555.0147</span></div>
  <div class="contact contact--email">
    <span class="contact__icon"><svg width="9" height="7" viewBox="0 0 9 7"><rect x=".5" y=".5" width="8" height="6" fill="none" stroke="#fff"/><path d="M.5 .5 L4.5 4 L8.5 .5" fill="none" stroke="#fff"/></svg></span>
    tkelwer@corvantshield.com
  </div>
  <div class="contact contact--web">
    <span class="contact__icon"><svg width="10" height="10" viewBox="0 0 10 10"><circle cx="5" cy="5" r="4.3" fill="none" stroke="#fff"/><ellipse cx="5" cy="5" rx="1.8" ry="4.3" fill="none" stroke="#fff"/><path d="M.7 5 H9.3" stroke="#fff"/></svg></span>
    corvantshield.com
  </div>
  <div class="social"><span></span><span></span></div>
</article>

<!-- Greyscale version -->
<article class="flyer flyer--mono">
  <svg class="flyer__art" viewBox="0 0 502 645">
    <defs>
      <linearGradient id="photoMono" x1="0" y1="0" x2="1" y2="0">
        <stop offset="0" stop-color="#f2f2f2"/><stop offset=".55" stop-color="#c6c6c6"/><stop offset="1" stop-color="#8d8d8d"/>
      </linearGradient>
      <linearGradient id="footMono" x1="0" y1="0" x2="0" y2="1">
        <stop offset="0" stop-color="#7a7a7a"/><stop offset="1" stop-color="#4a4a4a"/>
      </linearGradient>
    </defs>
    <rect x="0" y="0" width="502" height="272" fill="url(#photoMono)" role="img" aria-label="Photo, greyscale: smiling senior couple embracing in a bright home"/>
    <path d="M0 0 H275 C230 50 150 100 0 110 Z" fill="#fff"/>
    <path d="M288 0 C242 55 150 107 0 116" fill="none" stroke="#6e6e6e" stroke-width="2.5"/>
    <path d="M277 0 C232 51 150 101 0 111" fill="none" stroke="#1c1c1c" stroke-width="4"/>
    <path d="M0 262 C120 274 250 272 330 250 S460 218 502 224 V645 H0 Z" fill="#fff"/>
    <path d="M0 250 C120 262 250 260 330 238 S460 206 502 212" fill="none" stroke="#1c1c1c" stroke-width="6"/>
    <path d="M0 259 C120 271 250 269 330 247 S460 215 502 221" fill="none" stroke="#6e6e6e" stroke-width="3"/>
    <path d="M0 590 C120 555 250 560 330 575 S460 560 502 530 V645 H0 Z" fill="url(#footMono)"/>
    <path d="M0 578 C120 543 250 548 330 563 S460 547 502 518" fill="none" stroke="#1c1c1c" stroke-width="4"/>
  </svg>

  <div class="brand"><span class="brand__mark"></span>Corvant Shield</div>

  <h1 class="headline">
    <span class="headline__line headline__top">Our</span>
    <span class="headline__line headline__accent">Plans Are</span>
    <span class="headline__line headline__bottom">Based on Yours</span>
  </h1>

  <div class="benefits"></div>
  <div class="benefits__tab">Benefits:</div>
  <ul class="benefits__list">
    <li class="check">All plans we offer are state regulated</li>
    <li class="check">Relatively low monthly premiums</li>
    <li class="check">Premiums can never increase</li>
    <li class="check">Your policy can never be cancelled as long as you pay your premium</li>
    <li class="check">No medical exams</li>
    <li class="check">Guaranteed Death Benefit</li>
    <li class="check">Many policies we offer are Guaranteed Acceptance, "Day 1" coverage, have a child/grandchild rider and/or have an accelerated death benefit rider</li>
  </ul>

  <h2 class="section-title section-title--final">Final Expense Insurance</h2>
  <p class="copy copy--intro">Final Expense Insurance is a type of permanent whole life insurance insurance where the death benefit is used to cover (but not limited to) medical costs, funeral costs and other end-of-life expenses. It is a budget friendly option with a death benefit of up to $40k.</p>
  <table class="rates">
    <tr><th>Monthly premiums as low as</th><td>$11*</td></tr>
    <tr><th>Death Benefits as high as</th><td>$40,000</td></tr>
  </table>
  <p class="copy copy--p1">Unforeseen events and a lack of the right kind of insurance can spell trouble quickly. Contact us today, to set up a free assessment time. We will analyze your insurance needs and get you and your family the right coverage quickly at a budget friendly price.</p>
  <p class="copy copy--p2">We have been helping clients in Northern Idaho/Eastern Washington prepare for the unknown.</p>
  <p class="copy copy--p3">We have access to the industry's top insurance carriers so you can get the right coverage, that fits your budget.</p>
  <p class="copy copy--p4">Find out how we can give you the peace of mind of knowing your family will not have a financial burden if something were to happen to you.</p>

  <h2 class="section-title section-title--also">We Also Specialize In:</h2>
  <ul class="also-list">
    <li class="check">Medicare Supplement Insurance (Medigap)</li>
    <li class="check">Annuities</li>
    <li class="check">Mortgage Protection Insurance</li>
  </ul>
  <p class="footnote">*Based on an insured that is a 65 year old, non-smoking female that has no medical conditions with a death benefit of $2k</p>

  <div class="call"><span class="call__label">Call us now:</span><span class="call__phone">(208)555.0147</span></div>
  <div class="contact contact--email">
    <span class="contact__icon"><svg width="9" height="7" viewBox="0 0 9 7"><rect x=".5" y=".5" width="8" height="6" fill="none" stroke="#fff"/><path d="M.5 .5 L4.5 4 L8.5 .5" fill="none" stroke="#fff"/></svg></span>
    tkelwer@corvantshield.com
  </div>
  <div class="contact contact--web">
    <span class="contact__icon"><svg width="10" height="10" viewBox="0 0 10 10"><circle cx="5" cy="5" r="4.3" fill="none" stroke="#fff"/><ellipse cx="5" cy="5" rx="1.8" ry="4.3" fill="none" stroke="#fff"/><path d="M.7 5 H9.3" stroke="#fff"/></svg></span>
    corvantshield.com
  </div>
  <div class="social"><span></span><span></span></div>
</article>

</body>
</html>
```